"Jewelry Line Postcard Design"

Would like to describe what the line is about via a bio include a photo of me and the logo.

Target Market(s)

20-55

Industry/Entity Type

Jewelry

```html
<!DOCTYPE html>
<html lang="en">
<head>
<meta charset="utf-8">
<title>Visuri Înalte – Jewelry Line Postcard</title>
<link rel="stylesheet" href="https://fonts.googleapis.com/css2?family=Cinzel:wght@400;600&family=PT+Sans:wght@400&family=PT+Sans+Narrow:wght@700&display=swap">
<style>
  :root {
    --stage: #2b2b2b;
    --card: #ffffff;
    --ink: #1c1c1c;
    --magenta: #c2288f;
    --band-start: #c964b0;
    --band-end: #f1c9e3;
    --stamp: #f1e1ef;
    --white: #ffffff;
  }
  * { margin: 0; padding: 0; box-sizing: border-box; }
  html, body {
    width: 1200px; height: 1000px; overflow: hidden;
    background: var(--stage);
  }
  .canvas { position: relative; width: 1200px; height: 1000px; }

  .postcard {
    position: absolute; width: 724px; height: 560px;
    background: var(--card); overflow: hidden;
    font-family: "PT Sans", "Helvetica Neue", Arial, sans-serif;
    color: var(--ink);
  }
  .postcard--back { left: 39px; top: 44px; }
  .postcard--front { left: 456px; top: 418px;
    background: linear-gradient(160deg, #e6f3f8 0%, #ffffff 35%, #ffffff 70%, #f4f0f6 100%); }

  .brand-name {
    position: absolute;
    font-family: "PT Sans", "Helvetica Neue", Arial, sans-serif;
    font-size: 17px; font-weight: 400; letter-spacing: 2px;
    color: var(--ink); display: flex; align-items: center; gap: 8px;
    white-space: nowrap;
  }
  .brand-name__mark { width: 9px; height: 9px; background: var(--magenta); }

  .name-band {
    position: absolute; left: 0; height: 26px;
    background: linear-gradient(90deg, var(--band-start), var(--band-end));
    font-family: "PT Sans Narrow", "Arial Narrow", sans-serif;
    font-weight: 700; font-size: 19px; line-height: 26px;
    color: var(--white);
  }
  .email { position: absolute; font-size: 16px; }

  /* back side */
  .back__portrait {
    position: absolute; inset: 0;
    background:
      radial-gradient(ellipse 260px 300px at 50% 25%, #efe2dc 0%, #f6eeea 45%, rgba(255,255,255,0) 100%),
      linear-gradient(90deg, #ffffff 0%, #faf6f4 40%, #f7efe9 60%, #ffffff 100%);
  }
  .back__stamp { position: absolute; left: 558px; top: 31px; width: 129px; height: 135px; background: var(--stamp); }
  .back__brand { left: 39px; top: 145px; }
  .back__bio { position: absolute; left: 38px; top: 190px; width: 290px; font-size: 16.5px; line-height: 22.5px; }
  .back__band { top: 318px; width: 177px; padding-left: 39px; }
  .back__email { left: 39px; top: 355px; }
  .back__jewels {
    position: absolute; left: 46px; top: 380px; width: 140px; height: 92px;
    background: linear-gradient(180deg, #eadbbb, #d9bf86); opacity: .75;
  }

  /* front side */
  .front__splash {
    position: absolute; left: 0; top: 200px; width: 440px; height: 360px;
    background:
      radial-gradient(ellipse 140px 90px at 55% 40%, rgba(120,110,220,.45), rgba(255,255,255,0) 100%),
      radial-gradient(ellipse 160px 90px at 50% 70%, rgba(220,90,190,.35), rgba(255,255,255,0) 100%),
      radial-gradient(ellipse 120px 60px at 30% 95%, rgba(220,230,120,.35), rgba(255,255,255,0) 100%);
  }
  .front__portrait {
    position: absolute; right: 0; top: 0; width: 340px; height: 560px;
    background:
      radial-gradient(ellipse 120px 150px at 55% 32%, #d9d9d9 0%, #a9a9a9 60%, rgba(90,90,90,0) 100%),
      linear-gradient(90deg, rgba(255,255,255,0) 0%, #8a8a8a 20%, #3c3c3c 100%);
  }
  .front__brand { left: 50px; top: 64px; }
  .front__headline {
    position: absolute; left: 212px; top: 56px;
    font-family: "Cinzel", "Trajan Pro", serif; font-weight: 400;
    color: var(--ink); font-size: 28px; white-space: nowrap;
  }
  .front__headline em { font-style: normal; font-size: 44px; font-weight: 600; color: var(--magenta); }
  .front__story { position: absolute; left: 38px; top: 133px; width: 420px; font-size: 15px; line-height: 19.5px; }
  .front__quote-mark {
    position: absolute; left: 30px; top: 236px;
    font-family: "Cinzel", serif; font-size: 96px; font-weight: 600; line-height: 1;
  }
  .front__quote { position: absolute; left: 91px; top: 260px; width: 300px; font-size: 18.5px; line-height: 23.5px; }
  .front__band { top: 475px; width: 157px; padding-left: 39px; }
  .front__email { left: 39px; top: 512px; }
  .front__signature {
    position: absolute; left: 568px; top: 500px;
    font-family: "Cinzel", "Trajan Pro", serif; font-size: 22px; color: var(--white);
  }
</style>
</head>
<body>
<main class="canvas">

  <section class="postcard postcard--back" aria-label="Postcard back">
    <div class="back__portrait" role="img" aria-label="Soft faded portrait of the designer filling the card background"></div>
    <div class="back__stamp"></div>
    <div class="brand-name back__brand"><span class="brand-name__mark"></span>VISURI ÎNALTE</div>
    <p class="back__bio">Dr. Mara’s jewelry has been worn by stylists, designers, high profile TV personalities and anchors, as well as people who just want to look good and feel beautiful.</p>
    <div class="name-band back__band">Dr. Mara Lindqvist</div>
    <p class="email back__email">email: info@drmaralindqvist.com</p>
    <div class="back__jewels" role="img" aria-label="Gold earrings and statement necklace from the collection"></div>
  </section>

  <section class="postcard postcard--front" aria-label="Postcard front">
    <div class="front__splash" role="img" aria-label="Abstract watercolor splash in violet, pink and yellow"></div>
    <div class="front__portrait" role="img" aria-label="Black and white portrait of the designer"></div>
    <div class="brand-name front__brand"><span class="brand-name__mark"></span>VISURI ÎNALTE</div>
    <h1 class="front__headline">DREAM <em>BIG</em></h1>
    <p class="front__story">This Collection was based on the bold and dramatic costume pieces of the 60's and 70's. The Jewelry collection was named Visuri Înalte, which means dream big in Romanian, because we all deserve to live out our biggest dreams!</p>
    <span class="front__quote-mark" aria-hidden="true">“</span>
    <blockquote class="front__quote">It’s my goal to make every woman feel like her very best self, so she can go out into the world to sparkle and shine. To create a line of jewelry that’s both beautiful and purposeful is truly a dream come true.”</blockquote>
    <div class="name-band front__band">Dr. Mara Lindqvist</div>
    <p class="email front__email">email: drmara@drmaralindqvist.com</p>
    <p class="front__signature">DR. MARA</p>
  </section>

</main>
</body>
</html>
```